Brightline Energy Product Distribution Brochure

We are looking to have our current brochure for our customers completely redesigned...the idea is to present the relevant information in an attractive way . Our website is brightlineenergyco.example where you can find more information about us. We have included a file with a rough idea of the page order and what each should include but feel free to adapt based on design. The example provided is only for context and doesnt have to be maintained. We will be using the brochure both digitally and in print form. As long as it reads easily and is eye catching, the design can be horizontal or vertical.Final deliverable should be indesign file.

"Our Brands" page: should be limited to one page (space being enough) where it has the header for each one (for example diesel generators) space for one or two lines of text and then the corresponding logos for each of the five categories
Updates

For those asking: the "our brands" page should be a single page layout where there is a header with the corresponding section and space for maybe one line of text followed by the two logos for that category. Each of the product pages should be similar in fashion to the one in the document attached: a photo of the product with some white space and space for the text to be included. We will be posting additional examples today

Target Market(s)

We want to present it to customers both digitally and in print so they can see our products

Industry/Entity Type

Power Generation

Font styles to use
Serif

Requirements
Must have
• Eye catching and able to present the information in a presentable fashion. Rest is up to you.
Nice to have
• Should incorporate the colors of our logo but can also add other depending on design

```html
<!DOCTYPE html>
<html lang="en">
<head>
<meta charset="utf-8">
<title>Brightline Energy – Our Stock Pages</title>
<link rel="stylesheet" href="https://fonts.googleapis.com/css2?family=Raleway:wght@300;400;700&display=swap">
<style>
  :root{
    --charcoal:#3b3937;
    --yellow:#f6c700;
    --line-yellow:#e9be00;
    --white:#ffffff;
    --paper-shade:#e6e6e6;
    --muted:#b9b6b2;
    --footer-ink:#3b3937;
    --photo-tone:#d9d9d9;
  }
  html,body{margin:0;padding:0;width:1200px;height:1200px;overflow:hidden;background:var(--white);}
  .spread{position:relative;width:1200px;height:1200px;font-family:"Raleway",sans-serif;}
  .page-slot{position:absolute;width:378px;height:534px;box-shadow:0 10px 24px rgba(0,0,0,.22);}
  .page{position:absolute;left:0;top:0;width:473px;height:668px;transform:scale(.8);transform-origin:0 0;overflow:hidden;background:var(--white);}
  .page-art{position:absolute;inset:0;width:473px;height:668px;}
  .section-tag{position:absolute;left:0;top:30px;display:flex;align-items:center;gap:8px;}
  .section-tag .bar{width:40px;height:6px;background:var(--yellow);}
  .section-tag span{font-size:10px;font-weight:400;color:var(--muted);letter-spacing:.3px;}
  .brand{position:absolute;right:38px;top:27px;display:flex;align-items:center;gap:7px;}
  .brand .mark{width:14px;height:14px;background:var(--yellow);}
  .brand span{font-size:11px;font-weight:400;color:var(--white);letter-spacing:.4px;}
  .page-title{position:absolute;left:41px;top:78px;margin:0;font-size:27px;font-weight:300;color:var(--white);letter-spacing:.2px;white-space:nowrap;}
  .sub-heading{position:absolute;left:41px;top:134px;margin:0;font-size:14px;font-weight:700;color:var(--yellow);}
  .body-copy{position:absolute;left:41px;top:156px;width:185px;margin:0;font-size:7.6px;line-height:9.6px;font-weight:400;color:var(--muted);text-align:justify;}
  .product-photo{position:absolute;left:205px;top:325px;width:250px;height:240px;background:radial-gradient(ellipse at center,#8a8a8a 0%,#5a5a5a 45%,rgba(255,255,255,0) 72%);}
  .footer{position:absolute;left:40px;bottom:20px;display:flex;gap:36px;font-size:6.5px;font-weight:700;color:var(--footer-ink);}
</style>
</head>
<body>
<main class="spread">

  <!-- Row 1 -->
  <section class="page-slot" style="left:22px;top:42px;"><article class="page">
    <svg class="page-art" viewBox="0 0 473 668" aria-hidden="true">
      <polygon points="0,0 473,0 473,351 328,206 106,428 0,428" fill="var(--charcoal)"/>
      <polygon points="0,453 60,453 275,668 0,668" fill="var(--yellow)"/>
      <polygon points="473,590 473,668 395,668" fill="var(--paper-shade)"/>
      <polyline points="473,65 362,178 473,290" fill="none" stroke="var(--line-yellow)" stroke-width="1"/>
      <polyline points="0,255 100,355 0,455" fill="none" stroke="var(--line-yellow)" stroke-width="1"/>
    </svg>
    <div class="section-tag"><i class="bar"></i><span>OUR STOCK</span></div>
    <div class="brand"><i class="mark"></i><span>BRIGHTLINE ENERGY</span></div>
    <h2 class="page-title">PRIME GENERATORS</h2>
    <h3 class="sub-heading">CONTROLLERS</h3>
    <p class="body-copy">Our range covers reliable units for steady daily duty, built to keep sites running through long hours. Each model is tested before delivery and backed by trained field staff. Ask our team about sizing, fuel options, service plans and fast shipping to your location so your power stays on when it matters most.</p>
    <div class="product-photo" role="img" aria-label="Photo of a white trailer-mounted prime generator"></div>
    <div class="footer"><span>7</span><span>BRIGHTLINEENERGYCO.EXAMPLE</span></div>
  </article></section>

  <section class="page-slot" style="left:411px;top:42px;"><article class="page">
    <svg class="page-art" viewBox="0 0 473 668" aria-hidden="true">
      <polygon points="0,0 473,0 473,351 328,206 106,428 0,428" fill="var(--charcoal)"/>
      <polygon points="0,453 60,453 275,668 0,668" fill="var(--yellow)"/>
      <polygon points="473,590 473,668 395,668" fill="var(--paper-shade)"/>
      <polyline points="473,65 362,178 473,290" fill="none" stroke="var(--line-yellow)" stroke-width="1"/>
      <polyline points="0,255 100,355 0,455" fill="none" stroke="var(--line-yellow)" stroke-width="1"/>
    </svg>
    <div class="section-tag"><i class="bar"></i><span>OUR STOCK</span></div>
    <div class="brand"><i class="mark"></i><span>BRIGHTLINE ENERGY</span></div>
    <h2 class="page-title">RENTAL GENERATORS</h2>
    <h3 class="sub-heading">CONTROLLERS</h3>
    <p class="body-copy">Our range covers reliable units for steady daily duty, built to keep sites running through long hours. Each model is tested before delivery and backed by trained field staff. Ask our team about sizing, fuel options, service plans and fast shipping to your location so your power stays on when it matters most.</p>
    <div class="product-photo" role="img" aria-label="Photo of a black rental generator alternator unit"></div>
    <div class="footer"><span>8</span><span>BRIGHTLINEENERGYCO.EXAMPLE</span></div>
  </article></section>

  <section class="page-slot" style="left:800px;top:42px;"><article class="page">
    <svg class="page-art" viewBox="0 0 473 668" aria-hidden="true">
      <polygon points="0,0 473,0 473,351 328,206 106,428 0,428" fill="var(--charcoal)"/>
      <polygon points="0,453 60,453 275,668 0,668" fill="var(--yellow)"/>
      <polygon points="473,590 473,668 395,668" fill="var(--paper-shade)"/>
      <polyline points="473,65 362,178 473,290" fill="none" stroke="var(--line-yellow)" stroke-width="1"/>
      <polyline points="0,255 100,355 0,455" fill="none" stroke="var(--line-yellow)" stroke-width="1"/>
    </svg>
    <div class="section-tag"><i class="bar"></i><span>OUR STOCK</span></div>
    <div class="brand"><i class="mark"></i><span>BRIGHTLINE ENERGY</span></div>
    <h2 class="page-title">AC ALTERNATORS</h2>
    <h3 class="sub-heading">CONTROLLERS</h3>
    <p class="body-copy">Our range covers reliable units for steady daily duty, built to keep sites running through long hours. Each model is tested before delivery and backed by trained field staff. Ask our team about sizing, fuel options, service plans and fast shipping to your location so your power stays on when it matters most.</p>
    <div class="product-photo" role="img" aria-label="Photo of a black AC alternator"></div>
    <div class="footer"><span>9</span><span>BRIGHTLINEENERGYCO.EXAMPLE</span></div>
  </article></section>

  <!-- Row 2 -->
  <section class="page-slot" style="left:22px;top:620px;"><article class="page">
    <svg class="page-art" viewBox="0 0 473 668" aria-hidden="true">
      <polygon points="0,0 473,0 473,351 328,206 106,428 0,428" fill="var(--charcoal)"/>
      <polygon points="0,453 60,453 275,668 0,668" fill="var(--yellow)"/>
      <polygon points="473,590 473,668 395,668" fill="var(--paper-shade)"/>
      <polyline points="473,65 362,178 473,290" fill="none" stroke="var(--line-yellow)" stroke-width="1"/>
      <polyline points="0,255 100,355 0,455" fill="none" stroke="var(--line-yellow)" stroke-width="1"/>
    </svg>
    <div class="section-tag"><i class="bar"></i><span>OUR STOCK</span></div>
    <div class="brand"><i class="mark"></i><span>BRIGHTLINE ENERGY</span></div>
    <h2 class="page-title">ALTERNATOR PARTS</h2>
    <h3 class="sub-heading">CONTROLLERS</h3>
    <p class="body-copy">Our range covers reliable units for steady daily duty, built to keep sites running through long hours. Each model is tested before delivery and backed by trained field staff. Ask our team about sizing, fuel options, service plans and fast shipping to your location so your power stays on when it matters most.</p>
    <div class="product-photo" role="img" aria-label="Photo of an automatic voltage regulator circuit board on a clear stand"></div>
    <div class="footer"><span>10</span><span>BRIGHTLINEENERGYCO.EXAMPLE</span></div>
  </article></section>

  <section class="page-slot" style="left:411px;top:620px;"><article class="page">
    <svg class="page-art" viewBox="0 0 473 668" aria-hidden="true">
      <polygon points="0,0 473,0 473,351 328,206 106,428 0,428" fill="var(--charcoal)"/>
      <polygon points="0,453 60,453 275,668 0,668" fill="var(--yellow)"/>
      <polygon points="473,590 473,668 395,668" fill="var(--paper-shade)"/>
      <polyline points="473,65 362,178 473,290" fill="none" stroke="var(--line-yellow)" stroke-width="1"/>
      <polyline points="0,255 100,355 0,455" fill="none" stroke="var(--line-yellow)" stroke-width="1"/>
    </svg>
    <div class="section-tag"><i class="bar"></i><span>OUR STOCK</span></div>
    <div class="brand"><i class="mark"></i><span>BRIGHTLINE ENERGY</span></div>
    <h2 class="page-title">CONTROLLERS</h2>
    <h3 class="sub-heading">CONTROLLERS</h3>
    <p class="body-copy">Our range covers reliable units for steady daily duty, built to keep sites running through long hours. Each model is tested before delivery and backed by trained field staff. Ask our team about sizing, fuel options, service plans and fast shipping to your location so your power stays on when it matters most.</p>
    <div class="product-photo" role="img" aria-label="Photo of a black generator control module with a green display"></div>
    <div class="footer"><span>11</span><span>BRIGHTLINEENERGYCO.EXAMPLE</span></div>
  </article></section>

  <section class="page-slot" style="left:800px;top:620px;"><article class="page">
    <svg class="page-art" viewBox="0 0 473 668" aria-hidden="true">
      <polygon points="0,0 473,0 473,351 328,206 106,428 0,428" fill="var(--charcoal)"/>
      <polygon points="0,453 60,453 275,668 0,668" fill="var(--yellow)"/>
      <polygon points="473,590 473,668 395,668" fill="var(--paper-shade)"/>
      <polyline points="473,65 362,178 473,290" fill="none" stroke="var(--line-yellow)" stroke-width="1"/>
      <polyline points="0,255 100,355 0,455" fill="none" stroke="var(--line-yellow)" stroke-width="1"/>
    </svg>
    <div class="section-tag"><i class="bar"></i><span>OUR STOCK</span></div>
    <div class="brand"><i class="mark"></i><span>BRIGHTLINE ENERGY</span></div>
    <h2 class="page-title">TRANSFER SWITCHES</h2>
    <h3 class="sub-heading">CONTROLLERS</h3>
    <p class="body-copy">Our range covers reliable units for steady daily duty, built to keep sites running through long hours. Each model is tested before delivery and backed by trained field staff. Ask our team about sizing, fuel options, service plans and fast shipping to your location so your power stays on when it matters most.</p>
    <div class="product-photo" role="img" aria-label="Photo of a grey metal transfer switch cabinet"></div>
    <div class="footer"><span>12</span><span>BRIGHTLINEENERGYCO.EXAMPLE</span></div>
  </article></section>

</main>
</body>
</html>
```